ebook cover for The Heron & The Teapot (Plink!)

We would like an ebook cover for a post Ph.D. on Animal Totems book called The Heron and The Teapot. It is about human relationships and dating. Author is Marla Wendlow Ph.D.
I am thinking perhaps just typographic with a fancy custom italicized or handwriting kind of font that fills the whole page, or a picture that doesn't belittle the fairytale of love. Something cosmic.
The subtitle to guide people, small, is "on dating"

```html
<!DOCTYPE html>
<html lang="en">
<head>
<meta charset="utf-8">
<title>The Heron and The Teapot — Marla Wendlow Ph.D.</title>
<link rel="stylesheet" href="https://fonts.googleapis.com/css2?family=Bungee&family=Josefin+Sans:wght@700&display=swap">
<style>
  :root {
    --sky-top: #2b0b15;
    --sky-mid: #4a3a33;
    --sky-low: #7a7b5a;
    --glow: #ece9b8;
    --star: #eddcb0;
    --author: #f1dcb0;
    --metal-light: #f4f3d2;
    --metal-mid: #b9b98a;
    --metal-dark: #5f6040;
    --subtitle: #d9d7b4;
    --art-warm: #d58a5a;
    --art-gold: #d9c07a;
  }
  * { margin: 0; padding: 0; box-sizing: border-box; }
  html, body { width: 754px; height: 1200px; overflow: hidden; background: var(--sky-top); }
  .cover {
    position: relative;
    width: 754px;
    height: 1200px;
    overflow: hidden;
    background:
      radial-gradient(ellipse 420px 260px at 50% 940px, rgba(236,233,184,0.55), rgba(236,233,184,0) 70%),
      linear-gradient(180deg, var(--sky-top) 0%, #3a1e24 30%, var(--sky-mid) 48%, var(--sky-low) 70%, #8f9068 100%);
  }
  .stars { position: absolute; inset: 0; width: 754px; height: 1200px; }
  .stars polygon { fill: var(--star); }
  .author {
    position: absolute;
    top: 104px;
    left: 0;
    width: 100%;
    padding-left: 8px;
    text-align: center;
    font-family: "Josefin Sans", sans-serif;
    font-weight: 700;
    font-size: 42px;
    color: var(--author);
  }
  .title {
    position: absolute;
    top: 238px;
    left: 0;
    width: 100%;
    text-align: center;
    font-family: "Bungee", sans-serif;
    font-weight: 400;
    line-height: 1;
  }
  .title span {
    display: block;
    background: linear-gradient(180deg, var(--metal-light) 0%, var(--metal-mid) 45%, var(--metal-light) 60%, var(--metal-mid) 100%);
    -webkit-background-clip: text;
    background-clip: text;
    color: transparent;
    -webkit-text-stroke: 1.5px var(--metal-dark);
    filter: drop-shadow(2px 3px 2px rgba(0,0,0,0.55));
  }
  .title .line-main { font-size: 80px; letter-spacing: 2px; }
  .title .line-join { font-size: 54px; margin: 24px 0 30px; }
  .subtitle {
    position: absolute;
    top: 628px;
    left: 0;
    width: 100%;
    text-align: center;
    font-family: "Bungee", sans-serif;
    font-size: 36px;
    letter-spacing: 3px;
    color: var(--subtitle);
    text-shadow: 1px 2px 2px rgba(0,0,0,0.45);
  }
  .artwork {
    position: absolute;
    left: 0;
    bottom: 0;
    width: 754px;
    height: 450px;
    background: radial-gradient(ellipse 380px 300px at 50% 70%, rgba(217,192,122,0.55), rgba(213,138,90,0.25) 60%, rgba(213,138,90,0) 100%);
  }
</style>
</head>
<body>
  <main class="cover">
    <svg class="stars" viewBox="0 0 754 1200" aria-hidden="true">
      <defs>
        <polygon id="star" points="0,-14 4.1,-4.5 14,-4.3 6.4,2.2 8.7,12 0,6.6 -8.7,12 -6.4,2.2 -14,-4.3 -4.1,-4.5"/>
      </defs>
      <use href="#star" x="20" y="20"/>
      <use href="#star" x="192" y="68"/>
      <use href="#star" x="426" y="84"/>
      <use href="#star" x="632" y="52"/>
      <use href="#star" x="576" y="178"/>
      <use href="#star" x="708" y="194"/>
      <use href="#star" x="78" y="370"/>
      <use href="#star" x="250" y="394"/>
      <use href="#star" x="682" y="406"/>
    </svg>

    <p class="author">Marla Wendlow Ph.D.</p>

    <h1 class="title">
      <span class="line-main">The Heron</span>
      <span class="line-join">and</span>
      <span class="line-main">The Teapot</span>
    </h1>

    <p class="subtitle">on dating</p>

    <div class="artwork" role="img" aria-label="Illustration of a heron and a teapot side by side, softly lit against the evening glow"></div>
  </main>
</body>
</html>
```